Ridgeline Haul Carriers - Website

A clean, not cluttered informative website for our business. We specialize in the transportation of radioactive materials across North America. The site is mostly for information about our company and will not be used to attract business but will be used to attract employee's mainly drivers. Driver's are very hard to find in our area. One of the pages needs to be a job's posting page with an apply now button. Either an application can be filled out there or a resume can be uploaded which ever functionality works better. I would like a website that I can easily edit, ability to change text and photos.

Number of Pages Required

5+ page

Colors

Designer to choose colors to be used in the design.

Requirements
Must have
• Home - About - Services - Jobs - Contact pages
• A way prospective employee's can apply or upload their resume to be emailed to me
• Very clean apperance
Should not have
• I don't want it to be busy

```html
<!DOCTYPE html>
<html lang="en">
<head>
<meta charset="utf-8">
<title>Ridgeline Haul Carriers</title>
<link href="https://fonts.googleapis.com/css2?family=Mulish:wght@400;600;700;800&family=Open+Sans:wght@400;600&display=swap" rel="stylesheet">
<style>
:root{
  --orange:#f7941d;
  --orange-dark:#e5841a;
  --ink:#2b2b2b;
  --text:#444;
  --muted:#666;
  --band:#efefef;
  --line:#e6e6e6;
  --footer:#2d2d2d;
  --white:#fff;
}
*{box-sizing:border-box;margin:0;padding:0}
html,body{width:1200px;height:3077px;overflow:hidden}
body{position:relative;background:var(--white);font-family:'Mulish',sans-serif;color:var(--text)}
.abs{position:absolute}
.btn{position:absolute;display:flex;align-items:center;justify-content:center;border-radius:40px;font-weight:700;font-family:'Mulish',sans-serif;white-space:nowrap}
.btn-solid{background:var(--orange);color:var(--white)}
.btn-outline{border:2px solid var(--orange);color:var(--orange);background:var(--white)}
.btn-ghost{border:2px solid var(--white);color:var(--white)}

/* header */
.brand{position:absolute;left:140px;top:30px;display:flex;align-items:center;gap:12px;color:var(--orange);font-weight:800;font-size:26px;letter-spacing:1px;line-height:1.05}
.brand-mark{width:20px;height:20px;background:var(--orange);flex:none}
.main-nav{position:absolute;left:518px;top:36px;display:flex;gap:22px;font-size:17px;color:var(--ink)}
.login{left:906px;top:32px;width:154px;height:38px;font-size:15px;font-weight:600}

/* hero */
.hero{position:absolute;left:0;top:105px;width:1200px;height:512px;background:linear-gradient(180deg,#8d9196 0%,#a8a9a6 40%,#6e6d69 75%,#55524e 100%)}
.hero-panel{position:absolute;left:143px;top:130px;width:540px;height:295px;background:rgba(20,20,20,.72);border:1px solid rgba(255,200,120,.35)}
.hero-title{position:absolute;left:37px;top:62px;font-size:33px;font-weight:800;color:var(--white);white-space:nowrap;line-height:1.2}
.hero-sub{position:absolute;left:37px;top:115px;width:460px;font-size:19px;font-weight:700;line-height:36px;color:var(--white)}
.hero .learn{left:33px;top:196px;width:177px;height:48px;font-size:19px;font-weight:600}
.dots{position:absolute;left:578px;top:487px;display:flex;gap:4px}
.dots span{width:9px;height:9px;border-radius:50%;border:1px solid var(--white)}
.dots span.on{background:var(--orange);border-color:var(--orange)}

/* ratings */
.ratings{position:absolute;left:0;top:617px;width:1200px;height:116px;background:var(--band)}
.badge{position:absolute;top:34px;height:46px;border-radius:8px;background:#d9d9d9}

/* about */
.section-title{font-size:36px;font-weight:700;color:var(--ink);white-space:nowrap}
.about-title{left:150px;top:834px}
.about-sub{left:143px;top:896px;font-family:'Open Sans',sans-serif;font-size:16px;font-weight:600;color:#3a3a3a;white-space:nowrap}
.body-copy{font-family:'Open Sans',sans-serif;font-size:13px;line-height:27px;color:var(--text)}
.about-copy{left:145px;top:931px;width:425px}
.about .read{left:143px;top:1087px;width:119px;height:38px;font-size:15px}
.photo{position:absolute}
.about-photo{left:610px;top:846px;width:450px;height:290px;background:linear-gradient(180deg,#3c4250 0%,#c9873a 45%,#6b6a4a 65%,#4a5a3a 100%)}

/* services */
.services-photo{left:145px;top:1253px;width:636px;height:475px;background:linear-gradient(160deg,#2b3d66 0%,#5a6d92 40%,#b27a4a 65%,#3a3a3a 100%);box-shadow:0 6px 16px rgba(0,0,0,.3)}
.services-card{position:absolute;left:488px;top:1311px;width:570px;height:361px;background:var(--white);border:1px solid var(--line)}
.services-card .section-title{position:absolute;left:46px;top:30px}
.services-card .body-copy{position:absolute;left:48px;top:82px;width:480px}
.services-card .read{left:50px;top:284px;width:115px;height:36px;font-size:15px}

/* why */
.why{position:absolute;left:0;top:1846px;width:1200px;height:312px;background:var(--orange);text-align:center;color:var(--white)}
.why h2{position:absolute;left:0;top:68px;width:100%;font-size:32px;font-weight:700}
.why p{position:absolute;left:230px;top:126px;width:740px;font-size:18px;font-weight:600;line-height:32px}
.why .read{left:538px;top:216px;width:124px;height:36px;font-size:15px}

/* jobs */
.jobs-title{left:0;top:2238px;width:1200px;text-align:center}
.jobs-intro{left:320px;top:2287px;width:560px;text-align:center}
.job-card{position:absolute;top:2375px;width:440px;height:160px;border:1px solid var(--line);background:var(--white)}
.job-photo{position:absolute;left:20px;top:25px;width:109px;height:108px;background:linear-gradient(180deg,#6b5a48,#c7b8a0 60%,#5a5048)}
.job-card h3{position:absolute;left:145px;top:24px;font-size:18px;font-weight:600;color:var(--ink)}
.job-card p{position:absolute;left:145px;top:54px;width:280px;font-family:'Open Sans',sans-serif;font-size:12.5px;line-height:25px;color:var(--text)}
.job-card .apply{left:142px;top:112px;width:86px;height:26px;font-size:11.5px}
.job-card .upload{left:236px;top:112px;width:126px;height:26px;font-size:11.5px}
.view-all{left:548px;top:2573px;width:104px;height:32px;font-size:15px}

/* footer */
.footer-bg{position:absolute;left:0;top:2690px;width:1200px;height:387px}
.footer-brand{position:absolute;left:0;top:2770px;width:1200px;display:flex;justify-content:center;align-items:center;gap:12px;color:var(--white);font-weight:800;font-size:26px;letter-spacing:1px}
.footer-brand .brand-mark{background:var(--white);width:18px;height:18px}
.footer-nav{position:absolute;left:0;top:2850px;width:1200px;display:flex;justify-content:center;gap:24px;color:var(--white);font-size:15px;font-weight:700}
.social{position:absolute;left:574px;top:2901px;display:flex;gap:9px}
.social span{width:9px;height:9px;border-radius:50%;background:var(--white)}
.subscribe-label{position:absolute;left:0;top:2929px;width:1200px;text-align:center;color:var(--white);font-size:13px;font-family:'Open Sans',sans-serif}
.subscribe{position:absolute;left:458px;top:2958px;width:284px;height:48px;border-radius:30px;background:var(--white)}
.subscribe span{position:absolute;left:18px;top:15px;font-family:'Open Sans',sans-serif;font-size:13px;color:#777}
.subscribe .go{position:absolute;right:6px;top:8px;width:33px;height:33px;border-radius:50%;background:var(--orange)}
.copyright{position:absolute;left:0;top:3033px;width:1200px;text-align:center;color:var(--white);font-size:12.5px;font-family:'Open Sans',sans-serif}
</style>
</head>
<body>

<header>
  <div class="brand"><span class="brand-mark"></span><span>RIDGELINE HAUL<br>CARRIERS</span></div>
  <nav class="main-nav"><span>Home</span><span>About</span><span>Services</span><span>Jobs</span><span>Contact Us</span></nav>
  <a class="btn btn-outline login">Login / Register</a>
</header>

<section class="hero" role="img" aria-label="Photo of a transport truck hauling tanks in a parking lot">
  <div class="hero-panel">
    <h1 class="hero-title">RIDGELINE HAUL CARRIERS</h1>
    <p class="hero-sub">Sed ut perspiciatis unde omnis iste natusor sit voluptatem accusantium doloremque</p>
    <a class="btn btn-ghost learn">Learn More</a>
  </div>
  <div class="dots"><span class="on"></span><span></span><span></span><span></span></div>
</section>

<section class="ratings">
  <div class="badge" style="left:214px;width:156px"></div>
  <div class="badge" style="left:510px;width:140px"></div>
  <div class="badge" style="left:758px;width:188px"></div>
</section>

<section class="about">
  <h2 class="abs section-title about-title">ABOUT US</h2>
  <p class="abs about-sub">We Make our customers both satisfied and successful</p>
  <p class="abs body-copy about-copy">Ridgeline Haul Carriers has been providing quality transportation services since our founding in 1999. It is part of the Halvorsen Group of Companies. With a firm commitment to superior service and integrity above all, the team has developed an enviable reputation within the transportation industry.</p>
  <a class="btn btn-solid read">Read More</a>
  <div class="photo about-photo" role="img" aria-label="Photo of a truck on a highway at sunset"></div>
</section>

<section class="services">
  <div class="photo services-photo" role="img" aria-label="Photo of a semi truck driving at dusk"></div>
  <div class="services-card">
    <h2 class="section-title">OUR SERVICES</h2>
    <p class="body-copy">At Ridgeline Haul Carriers, we specialize in both expedited and regular LTL, Partial Load and Full Truck Load service between Canada, the USA, and Mexico. In addition, to meet our just in time door to door service requirements, our policy includes one line hauls right to your delivery, which eliminates extra handling of your products which also in turn reduces damages and claims. When looking for someone to move your cargo to its destination on time and damage free, call Ridgeline Haul Carriers at 888-555-0142.</p>
    <a class="btn btn-solid read">Read More</a>
  </div>
</section>

<section class="why">
  <h2>WHY CHOOSE US</h2>
  <p>Sed ut perspiciatis unde omnis iste natus aerror sit voluptatem accusantium dolor aemque laudantium, totam rem aperiam, eaque ipsa quae</p>
  <a class="btn btn-ghost read">Read More</a>
</section>

<section class="jobs">
  <h2 class="abs section-title jobs-title">OUR JOBS</h2>
  <p class="abs body-copy jobs-intro">Ridgeline Haul Carriers is an international carrier which provides service between Canada and the United States with domestic service in each country.</p>
  <article class="job-card" style="left:103px">
    <div class="job-photo" role="img" aria-label="Photo of a driver at the wheel"></div>
    <h3>Sed ut perspiciat</h3>
    <p>Lorem ipsum dolor sit amet, consectetur adip scing elit, sed do eiusmod tempor.</p>
    <a class="btn btn-solid apply">Apply Now</a>
    <a class="btn btn-outline upload">Upload Resume</a>
  </article>
  <article class="job-card" style="left:576px">
    <div class="job-photo" role="img" aria-label="Photo of a driver in a truck cab"></div>
    <h3>Sed ut perspiciat</h3>
    <p>Lorem ipsum dolor sit amet, consectetur adip scing elit, sed do eiusmod tempor.</p>
    <a class="btn btn-solid apply">Apply Now</a>
    <a class="btn btn-outline upload">Upload Resume</a>
  </article>
  <a class="btn btn-solid view-all">View All</a>
</section>

<footer>
  <svg class="footer-bg" viewBox="0 0 1200 387" preserveAspectRatio="none" aria-hidden="true">
    <path d="M0 100 Q600 -50 1200 100 L1200 387 L0 387 Z" fill="#2d2d2d"/>
  </svg>
  <div class="footer-brand"><span class="brand-mark"></span><span>RIDGELINE HAUL CARRIERS</span></div>
  <nav class="footer-nav"><span>Home</span><span>About</span><span>Services</span><span>Jobs</span><span>Contact Us</span></nav>
  <div class="social"><span></span><span></span><span></span></div>
  <p class="subscribe-label">Subscribe To Our Mailing List</p>
  <div class="subscribe">
    <span>Enter Your email Address</span>
    <svg class="go" viewBox="0 0 33 33" aria-hidden="true"><path d="M10 16.5h12M18 12l4.5 4.5L18 21" stroke="#fff" stroke-width="2.2" fill="none" stroke-linecap="round" stroke-linejoin="round"/></svg>
  </div>
  <p class="copyright">Copyright © 2019. All Rights Reserved | Terms of Use | Policy</p>
</footer>

</body>
</html>
```